Business Card for Fashion House

We need a business card design for our personalize fashion service for our customers. the business card should reflect reliability, luxury and creativity.
The brand Gravetto is extracted from "Graceful Velvetto"; Gravetto provides fashion designs sprinkled with luxury and style tailored for our elite clients character profile.
Gravetto is created for those who embody class and elegance with a passion for style.
Target Market(s)
Affluent Customers
Industry/Entity Type
Fashion
Contact Information for Business Card
Samira Haddadin
Fashion Designer
Telephone: +971 4 555 0192
Mobile +971 50 555 0147
Emal info@gravetto-example.com
Website www.gravetto-example.com
Social Media Youtube g+ Facebook Instagram Pin /gravetto
Font styles to use
Other font styles liked:
- Audrey provided
Look and feel
Each slider illustrates characteristics of the customer's brand and the style your logo design should communicate.

```html
<!DOCTYPE html>
<html lang="en">
<head>
<meta charset="utf-8">
<title>Gravetto Business Card</title>
<link rel="stylesheet" href="https://fonts.googleapis.com/css2?family=Marcellus&family=Cormorant+Garamond:ital,wght@1,500&display=swap">
<style>
  :root {
    --backdrop: #141414;
    --card: #0b0b0b;
    --card-sheen: #1c1c1c;
    --ink: #f2f2f2;
    --ink-soft: #cfcfcf;
    --mark-faint: rgba(255, 255, 255, 0.06);
  }
  * { margin: 0; padding: 0; box-sizing: border-box; }
  html, body { width: 1200px; height: 864px; overflow: hidden; }
  body {
    background: var(--backdrop);
    font-family: "Marcellus", serif;
    color: var(--ink);
    position: relative;
  }
  .card {
    position: absolute;
    top: 289px;
    width: 500px;
    height: 286px;
    background: linear-gradient(135deg, var(--card-sheen) 0%, var(--card) 55%, var(--card) 100%);
    overflow: hidden;
    box-shadow: 0 10px 30px rgba(0, 0, 0, 0.6);
  }
  .card--front { left: 70px; }
  .card--back { left: 630px; }

  /* Front */
  .brand {
    position: absolute;
    left: 52px;
    top: 30px;
    width: 160px;
    text-align: center;
  }
  .brand__square {
    display: block;
    width: 26px;
    height: 26px;
    border: 2px solid var(--ink);
    margin: 0 auto 14px;
  }
  .brand__name {
    font-size: 17px;
    letter-spacing: 6px;
    text-transform: uppercase;
  }
  .holder {
    position: absolute;
    left: 48px;
    top: 112px;
  }
  .holder__name {
    font-size: 15px;
    letter-spacing: 0.5px;
    text-transform: uppercase;
  }
  .holder__title {
    font-family: "Cormorant Garamond", serif;
    font-style: italic;
    font-weight: 500;
    font-size: 13px;
    color: var(--ink-soft);
  }
  .divider {
    position: absolute;
    height: 2px;
    background: var(--ink);
  }
  .card--front .divider { left: 150px; right: 0; top: 148px; }
  .contacts {
    position: absolute;
    left: 30px;
    top: 170px;
    list-style: none;
    font-size: 12.5px;
    letter-spacing: 0.6px;
  }
  .contacts li {
    display: flex;
    align-items: center;
    gap: 9px;
    height: 22px;
  }
  .contacts svg { width: 13px; height: 13px; flex: none; }
  .faint-disc {
    position: absolute;
    right: 40px;
    top: 92px;
    width: 170px;
    height: 170px;
    border-radius: 50%;
    border: 14px solid var(--mark-faint);
  }

  /* Back */
  .card--back .divider { left: 0; width: 230px; top: 126px; }
  .back-name {
    position: absolute;
    left: 248px;
    top: 116px;
    font-size: 22px;
    letter-spacing: 10px;
    text-transform: uppercase;
  }
</style>
</head>
<body>
  <section class="card card--front" aria-label="Card front">
    <div class="faint-disc" aria-hidden="true"></div>
    <div class="brand">
      <span class="brand__square" aria-hidden="true"></span>
      <div class="brand__name">Gravetto</div>
    </div>
    <div class="holder">
      <div class="holder__name">Samira Haddadin</div>
      <div class="holder__title">Fashion Designer</div>
    </div>
    <div class="divider"></div>
    <ul class="contacts">
      <li>
        <svg viewBox="0 0 16 16" fill="none" stroke="currentColor" stroke-width="1.4"><circle cx="8" cy="8" r="7"/><path d="M5 5.5c0 3 2.5 5.5 5.5 5.5l.5-1.5-1.8-.8-.7.8c-1-.5-1.8-1.3-2.3-2.3l.8-.7-.8-1.8z" fill="currentColor" stroke="none"/></svg>
        +971 4 555 0192
      </li>
      <li>
        <svg viewBox="0 0 16 16" fill="none" stroke="currentColor" stroke-width="1.4"><circle cx="8" cy="8" r="7"/><rect x="5.7" y="4" width="4.6" height="8" rx="0.8"/></svg>
        +971 50 555 0147
      </li>
      <li>
        <svg viewBox="0 0 16 16" fill="none" stroke="currentColor" stroke-width="1.4"><circle cx="8" cy="8" r="7"/><rect x="4.5" y="5.5" width="7" height="5"/><path d="M4.5 5.5 8 8.3l3.5-2.8"/></svg>
        info@gravetto-example.com
      </li>
      <li>
        <svg viewBox="0 0 16 16" fill="none" stroke="currentColor" stroke-width="1.4"><circle cx="8" cy="8" r="7"/><path d="M1 8h14M8 1c2.5 2.5 2.5 11.5 0 14M8 1c-2.5 2.5-2.5 11.5 0 14"/></svg>
        www.gravetto-example.com
      </li>
    </ul>
  </section>

  <section class="card card--back" aria-label="Card back">
    <div class="divider"></div>
    <div class="back-name">Gravetto</div>
  </section>
</body>
</html>
```